Harrow Grading LLC business card design

Excavation company business cards

Contact Information for Business Card

Harrow Grading LLC cell phone 208-417-6290 office phone 208-319-4856 harrowgradingllc@maplecove.com Driveways, site prep, retaining walls, septic systems, rock delivery

Colors

Designer to choose colors to be used in the design.

```html
<!DOCTYPE html>
<html lang="en">
<head>
<meta charset="utf-8">
<title>Harrow Grading LLC — Business Card</title>
<link href="https://fonts.googleapis.com/css2?family=Roboto:wght@400;700&display=swap" rel="stylesheet">
<style>
  :root {
    --bg: #c9c9c9;
    --card-white: #ffffff;
    --card-grey: #666666;
    --brand-orange: #ee6a1f;
    --ink: #2b2b2b;
    --edge-grey: #5a5a5a;
    --divider: #8a8a8a;
    --emboss: #3f3f3f;
  }
  * { margin: 0; padding: 0; box-sizing: border-box; }
  html, body { width: 1200px; height: 788px; overflow: hidden; }
  body {
    background: var(--bg);
    font-family: "Roboto", Arial, sans-serif;
    display: flex;
    align-items: center;
    justify-content: center;
    gap: 40px;
  }
  .card {
    position: relative;
    width: 560px;
    height: 320px;
    overflow: hidden;
    box-shadow: 0 10px 24px rgba(0,0,0,.25);
  }
  .card--front { background: var(--card-white); }
  .card--back {
    background: var(--card-grey);
    display: flex;
    align-items: center;
    justify-content: center;
  }

  .brand {
    font-weight: 700;
    white-space: nowrap;
    line-height: 1;
  }
  .card--front .brand {
    position: absolute;
    left: 40px;
    top: 52px;
    width: 480px;
    color: var(--brand-orange);
    font-size: 40px;
    letter-spacing: .5px;
  }
  .card--back .brand {
    color: var(--emboss);
    font-size: 48px;
    letter-spacing: .5px;
  }

  .person { position: absolute; left: 40px; top: 176px; }
  .person__name {
    color: var(--brand-orange);
    font-weight: 700;
    font-size: 24px;
    letter-spacing: .5px;
  }
  .person__role {
    color: var(--ink);
    font-size: 17px;
    margin-top: 4px;
    padding-left: 2px;
  }

  .divider {
    position: absolute;
    left: 262px;
    top: 146px;
    width: 1px;
    height: 104px;
    background: var(--divider);
  }

  .contacts {
    position: absolute;
    left: 284px;
    top: 142px;
    list-style: none;
    color: var(--ink);
    font-size: 15px;
  }
  .contacts li { display: flex; align-items: center; gap: 8px; height: 27px; }
  .contacts svg { width: 12px; height: 12px; flex: none; }

  .band {
    position: absolute;
    left: 0;
    right: 0;
    bottom: 0;
    height: 14px;
    display: flex;
  }
  .band__end { width: 70px; background: var(--edge-grey); }
  .band__fill { flex: 1; background: var(--brand-orange); }
</style>
</head>
<body>
  <section class="card card--front" aria-label="Card front">
    <div class="brand">Harrow Grading LLC</div>

    <div class="person">
      <div class="person__name">DALE WHITCOMB</div>
      <div class="person__role">Founder</div>
    </div>

    <div class="divider"></div>

    <ul class="contacts">
      <li>
        <svg viewBox="0 0 12 12" aria-hidden="true"><path d="M2.5 1h2l1 2.5-1.3.9a6 6 0 0 0 3.4 3.4l.9-1.3 2.5 1v2a1 1 0 0 1-1 1A9 9 0 0 1 1.5 2a1 1 0 0 1 1-1z" fill="var(--brand-orange)"/></svg>
        208-319-4856
      </li>
      <li>
        <svg viewBox="0 0 12 12" aria-hidden="true"><rect x="3" y="0.8" width="6" height="10.4" rx="1" fill="none" stroke="var(--brand-orange)" stroke-width="1.3"/></svg>
        208-417-6290
      </li>
      <li>
        <svg viewBox="0 0 12 12" aria-hidden="true"><rect x="0.8" y="2.5" width="10.4" height="7" fill="var(--brand-orange)"/><path d="M1 3l5 3.5L11 3" fill="none" stroke="#fff" stroke-width="1"/></svg>
        harrowgradingllc@maplecove.com
      </li>
      <li>
        <svg viewBox="0 0 12 12" aria-hidden="true"><circle cx="6" cy="6" r="5.2" fill="var(--brand-orange)"/><path d="M1 6h10M6 1c2 2.5 2 7.5 0 10M6 1c-2 2.5-2 7.5 0 10" fill="none" stroke="#fff" stroke-width=".8"/></svg>
        www.harrowgradingco.net
      </li>
    </ul>

    <div class="band">
      <div class="band__end"></div>
      <div class="band__fill"></div>
      <div class="band__end"></div>
    </div>
  </section>

  <section class="card card--back" aria-label="Card back">
    <div class="brand">Harrow Grading LLC</div>
  </section>
</body>
</html>
```